hello! I need a very simple modern business card for a new venture called The Quiet Harbour Retreats. It's the very first Tech-Free retreat in Asia!

The concept is very unique. Basically a group of 12-15 people would go on a 3 to 4 days retreat where no phone or internet is allowed. The first retreat will take place in a beautiful villa in Bali by the sea. It will include yoga, meditation, art & writing workshops, swimming, hiking, cooking, healthy vegetarian meals, etc.

Reason: Thanks for your submissions. I still haven't found exactly what I'm after but the designs that haven't be eliminated are getting close.. Please keep in mind that it should be a simple, modern and upmarket business card. Thanks

Target Market(s)

Both men and women who would like to disconnect from life, computer and phone for 3/4 days. They can be either local or expats but based in Asia (Singapore, Hong Kong).
Client will have to pay for their own flight and then the price is around US$600 for a 3-day retreat including everything (accommodation, food, activities). It means clients already have a good income. They are usually working in marketing, advertising, digital media, public relations.

Industry/Entity Type

Internet

Font styles to use
Other font styles liked:
• anything modern you like

Colors
acd036
9bcb3c
f37022
f68d4d
1b1b1b
333333
acd037

Requirements
Must have
• Name: Rell Vonta
Position: #screenwanderer
Company: The Quiet Harbour Retreats (asia should be smaller than the rest)
- Email button - quietharbourretreats@mailora.com
- Pagenook button - www.pagenook.com/quietharbourretreats
- Ticketvale button - www.quietharbourretreats.ticketvale.com
Nice to have
• You can use my logo attached but it's something I designed quickly on Power Point so it would be nice to include your own version.
Should not have
• anything tacky or girly or childish. thanks

```html
<!DOCTYPE html>
<html lang="en">
<head>
<meta charset="utf-8">
<title>The Quiet Harbour Retreats — Business Card</title>
<link rel="stylesheet" href="https://fonts.googleapis.com/css2?family=Questrial&display=swap">
<style>
  :root {
    --orange: #ec6d31;
    --orange-light: #f68d4d;
    --green: #9bcb3c;
    --green-deep: #7fae2c;
    --ink: #1b1b1b;
    --ink-soft: #333333;
    --paper: #ffffff;
    --backdrop: #eef0f0;
    --pagenook-blue: #3b5a9a;
  }
  * { box-sizing: border-box; margin: 0; padding: 0; }
  html, body {
    width: 1200px; height: 1000px; overflow: hidden;
    background: var(--backdrop);
    font-family: "Questrial", "Century Gothic", sans-serif;
  }
  .sheet {
    position: relative; width: 1200px; height: 1000px;
    display: flex; align-items: center; justify-content: center; gap: 44px;
  }
  .card {
    position: relative; width: 540px; height: 320px;
    box-shadow: 0 2px 8px rgba(0,0,0,0.18);
  }
  /* Front */
  .card--front { background: var(--orange); display: flex; align-items: center; justify-content: center; }
  .brand { display: flex; align-items: center; gap: 14px; }
  .brand__dot { width: 22px; height: 22px; border-radius: 50%; background: var(--green); flex: none; }
  .brand__name {
    color: var(--paper); font-size: 27px; letter-spacing: 0.5px; line-height: 1;
  }
  /* Back */
  .card--back { background: var(--paper); }
  .card--back .brand { position: absolute; left: 34px; top: 40px; }
  .card--back .brand__name { color: var(--green-deep); font-size: 25px; }
  .person { position: absolute; right: 46px; top: 110px; text-align: right; }
  .person__name {
    color: var(--orange); font-size: 22px; font-variant: small-caps;
    letter-spacing: 1.5px; line-height: 1.1;
  }
  .person__role { color: var(--ink-soft); font-size: 16px; margin-top: 4px; }
  .contacts {
    position: absolute; right: 46px; top: 198px; list-style: none; text-align: right;
  }
  .contact {
    display: flex; align-items: center; justify-content: flex-end; gap: 9px;
    color: var(--ink); font-size: 14.5px; line-height: 28px;
  }
  .contact__icon { width: 19px; height: 19px; flex: none; display: block; }
  .contact__square { width: 19px; height: 19px; flex: none; border-radius: 2px; }
  .contact__square--pagenook { background: var(--pagenook-blue); }
  .contact__square--ticketvale { background: var(--orange-light); }
</style>
</head>
<body>
  <main class="sheet">
    <section class="card card--front" aria-label="Card front">
      <div class="brand">
        <span class="brand__dot"></span>
        <span class="brand__name">The Quiet Harbour Retreats</span>
      </div>
    </section>

    <section class="card card--back" aria-label="Card back">
      <div class="brand">
        <span class="brand__dot"></span>
        <span class="brand__name">The Quiet Harbour Retreats</span>
      </div>

      <div class="person">
        <p class="person__name">Rell Vonta</p>
        <p class="person__role">#screenwanderer</p>
      </div>

      <ul class="contacts">
        <li class="contact">
          <span>quietharbourretreats@mailora.com</span>
          <svg class="contact__icon" viewBox="0 0 20 20" aria-hidden="true">
            <rect x="1" y="4" width="18" height="12" rx="1.5" fill="#9bcb3c"/>
            <polyline points="2,5.5 10,11 18,5.5" fill="none" stroke="#ffffff" stroke-width="1.6"/>
          </svg>
        </li>
        <li class="contact">
          <span>www.pagenook.com/quietharbourretreats</span>
          <span class="contact__square contact__square--pagenook"></span>
        </li>
        <li class="contact">
          <span>www.quietharbourretreats.ticketvale.com</span>
          <span class="contact__square contact__square--ticketvale"></span>
        </li>
      </ul>
    </section>
  </main>
</body>
</html>
```